Allied Health team of Physiotherapists & Occupational Therapists seek a business card design

We have our new logo, we now need our new business cards and stationary. Tidewell: Oedema & Family Clinic is seeking a generic card design to represent our whole team and individual cards for each therapist that incorporates our new logo to communicate our holistic approach that is calming, nuturing, supportive and welcoming.
Our Physiotherapists and Occupational Therapists assess, treat and provide education for people who are at risk of or who have lymphoedema. This is often as a result of treatment for cancer. We provide pre-operative and post-operative management and cancer rehabilitation in our Pilates studio. Our team also consists of Physiotherapists who have a strong interest in pelvic floor and continence management for both men and women.

Target Market(s)

Mainly women health conscious

Industry/Entity Type

Allied Health: Physiotherapy / Occupational Therapy

Contact Information for Business Card

Address: 14 Gallivant Ave Marlowe Bay 3287 Phone: 84316570 fax: 8431 6578 Email: info@tidewellcareservices.com.au Website: tidewellcareservices.com.au Facebook address: facebook.com/TidewellOedemaAndFamilyCareClinic. Room to write appointments. Individual cards need to have name, office email and individual email and professional details

Requirements
Must have
• Logo as per uploaded documents

```html
<!DOCTYPE html>
<html lang="en">
<head>
<meta charset="utf-8">
<title>Tidewell business cards</title>
<link rel="stylesheet" href="https://fonts.googleapis.com/css2?family=Merriweather:wght@700&family=Roboto:ital,wght@0,400;1,400&display=swap">
<style>
  :root {
    --backdrop: #1e1e1e;
    --card: #efefee;
    --card-shade: #e4e4e3;
    --terracotta: #d58a5e;
    --sage: #8e9d93;
    --ink: #2c2c2c;
    --leaf-faint: rgba(200, 200, 198, 0.35);
  }
  * { box-sizing: border-box; margin: 0; padding: 0; }
  html, body { width: 1200px; height: 1138px; overflow: hidden; }
  body {
    background: var(--backdrop);
    position: relative;
    font-family: "Roboto", Arial, sans-serif;
    color: var(--ink);
  }
  .card {
    position: absolute;
    width: 620px;
    height: 375px;
    border-radius: 14px;
    background: linear-gradient(180deg, var(--card) 0%, var(--card) 55%, var(--card-shade) 100%);
    overflow: hidden;
  }
  .card--front { left: 274px; top: 186px; }
  .card--back { left: 276px; top: 608px; }

  .decor-leaves {
    position: absolute;
    left: 60px;
    top: 20px;
    width: 560px;
    height: 340px;
    border-radius: 50% 50% 0 0;
    background: radial-gradient(ellipse at 70% 40%, var(--leaf-faint) 0%, rgba(200,200,198,0) 65%);
  }

  .brand {
    position: absolute;
    text-align: center;
    font-family: "Roboto", Arial, sans-serif;
    font-weight: 400;
    color: var(--terracotta);
    line-height: 1.25;
  }
  .card--front .brand { left: 170px; top: 150px; width: 280px; font-size: 34px; }
  .card--back .brand { left: 34px; top: 160px; width: 240px; font-size: 28px; }
  .brand .brand-line { display: block; }
  .brand .brand-sub { font-size: 0.5em; letter-spacing: 0.12em; text-transform: uppercase; }

  .band {
    position: absolute;
    left: 0; right: 0; bottom: 0;
    height: 13px;
    display: flex;
  }
  .band span { flex: 1; }
  .band .band-terracotta { background: var(--terracotta); }
  .band .band-sage { background: var(--sage); }

  .details { position: absolute; left: 295px; top: 78px; }
  .name {
    font-family: "Merriweather", Georgia, serif;
    font-weight: 700;
    font-size: 20px;
    color: var(--terracotta);
    margin-bottom: 5px;
  }
  .role { font-style: italic; font-size: 15.5px; line-height: 19px; }
  .speciality { font-size: 15.5px; line-height: 19px; }

  .contacts { list-style: none; margin-top: 30px; font-size: 17px; }
  .contacts li { display: flex; align-items: center; height: 24px; }
  .contacts svg { width: 15px; height: 15px; fill: var(--terracotta); margin-right: 12px; flex: none; }
  .contacts .gap { margin-left: 22px; }
</style>
</head>
<body>
  <section class="card card--front">
    <div class="decor-leaves" role="img" aria-label="Faint leaf-sprig decoration"></div>
    <div class="brand">
      <span class="brand-line">Tidewell</span>
      <span class="brand-line brand-sub">Oedema &amp; Family Clinic</span>
    </div>
    <div class="band"><span class="band-terracotta"></span><span class="band-sage"></span></div>
  </section>

  <section class="card card--back">
    <div class="decor-leaves" role="img" aria-label="Faint leaf-sprig decoration"></div>
    <div class="brand">
      <span class="brand-line">Tidewell</span>
      <span class="brand-line brand-sub">Oedema &amp; Family Clinic</span>
    </div>
    <div class="details">
      <h1 class="name">Mirela Austin</h1>
      <p class="role">Physiotherapist</p>
      <p class="speciality">Lymphoedema &amp; Oncology Rehabilitation</p>
      <p class="speciality">Continence &amp; Pelvic Floor</p>
      <ul class="contacts">
        <li>
          <svg viewBox="0 0 16 16"><path d="M2 6c0-2 2-3 6-3s6 1 6 3v1h-3V5.5H5V7H2z M4 8h8l1.5 5h-11z"/></svg>8431 6570
          <svg class="gap" viewBox="0 0 16 16"><path d="M2 6c0-2 2-3 6-3s6 1 6 3v1h-3V5.5H5V7H2z M4 8h8l1.5 5h-11z"/></svg>8431 6578
        </li>
        <li>
          <svg viewBox="0 0 16 16"><path d="M1 4h14v9H1z" fill="none" stroke="#d58a5e" stroke-width="1.5"/><path d="M1 4l7 5 7-5" fill="none" stroke="#d58a5e" stroke-width="1.5"/></svg>info@tidewellcareservices.com.au
        </li>
        <li>
          <svg viewBox="0 0 16 16"><g fill="none" stroke="#d58a5e" stroke-width="1.3"><circle cx="8" cy="8" r="6.3"/><ellipse cx="8" cy="8" rx="2.8" ry="6.3"/><path d="M1.7 8h12.6M3 4.5h10M3 11.5h10"/></g></svg>www.tidewellcareservices.com.au
        </li>
        <li>
          <svg viewBox="0 0 16 16"><path d="M8 1a5 5 0 0 1 5 5c0 4-5 9-5 9S3 10 3 6a5 5 0 0 1 5-5zm0 3a2 2 0 1 0 0 4 2 2 0 0 0 0-4z"/></svg>14 Gallivant Ave, Marlowe Bay 3287
        </li>
      </ul>
    </div>
  </section>
</body>
</html>
```